Veldmark Supplies Business Card

Professional business card that stand out to our potential customers. Front and back with clean modern design

Industry/Entity Type

Oil and gas

Contact Information for Business Card

Name, address, website , office phone and cell number

Requirements
Must have
• Editable files for each employee

```html
<!DOCTYPE html>
<html lang="en">
<head>
<meta charset="utf-8">
<title>Veldmark Supplies Business Card</title>
<link rel="stylesheet" href="https://fonts.googleapis.com/css2?family=Montserrat:wght@400;500;700;800&display=swap">
<style>
  :root {
    --brand-red: #ec2227;
    --brand-cyan: #1fa9cf;
    --paper: #ffffff;
    --ink: #1b1b1b;
    --stage: #2b2b2b;
  }
  * { box-sizing: border-box; margin: 0; padding: 0; }
  html, body { width: 1200px; height: 875px; overflow: hidden; }
  body {
    background: var(--stage);
    font-family: "Montserrat", sans-serif;
    display: flex;
    align-items: center;
    justify-content: center;
    gap: 40px;
  }
  .card {
    width: 540px;
    height: 309px;
    border-radius: 22px;
    position: relative;
    overflow: hidden;
  }
  .card--front {
    background: var(--brand-red);
    display: flex;
    align-items: center;
    justify-content: center;
  }
  .wordmark {
    display: flex;
    align-items: center;
    gap: 14px;
    font-weight: 800;
    text-transform: uppercase;
    letter-spacing: 2px;
  }
  .wordmark__square { display: block; }
  .card--front .wordmark { color: var(--paper); font-size: 34px; }
  .card--front .wordmark__square { width: 34px; height: 34px; background: var(--paper); }

  .card--back { background: var(--paper); color: var(--ink); }
  .card--back .wordmark {
    position: absolute;
    top: 52px;
    left: 0;
    right: 0;
    justify-content: center;
    color: var(--brand-red);
    font-size: 26px;
  }
  .card--back .wordmark__square { width: 26px; height: 26px; background: var(--brand-cyan); }

  .details {
    position: absolute;
    top: 128px;
    left: 40px;
    right: 30px;
    display: flex;
    align-items: center;
  }
  .person {
    width: 200px;
    text-align: right;
    padding-right: 20px;
  }
  .person__name { color: var(--brand-red); font-weight: 700; font-size: 25px; line-height: 1.1; }
  .person__title { font-size: 13px; font-weight: 500; margin-top: 3px; }
  .divider { width: 1.5px; height: 96px; background: var(--brand-red); }
  .contacts { list-style: none; padding-left: 18px; }
  .contacts li {
    display: flex;
    align-items: center;
    gap: 9px;
    font-size: 13px;
    font-weight: 500;
    line-height: 23px;
  }
  .contacts svg { width: 12px; height: 12px; fill: var(--brand-cyan); flex: none; }
  .address {
    position: absolute;
    bottom: 36px;
    left: 0;
    right: 0;
    text-align: center;
    font-size: 13px;
    font-weight: 500;
  }
</style>
</head>
<body>
  <section class="card card--front" aria-label="Card front">
    <div class="wordmark"><span class="wordmark__square"></span>Veldmark Supplies</div>
  </section>

  <section class="card card--back" aria-label="Card back">
    <div class="wordmark"><span class="wordmark__square"></span>Veldmark Supplies</div>
    <div class="details">
      <div class="person">
        <p class="person__name">Arlen Voss</p>
        <p class="person__title">President</p>
      </div>
      <div class="divider"></div>
      <ul class="contacts">
        <li><svg viewBox="0 0 24 24" aria-hidden="true"><path d="M4 9c0-3 4-5 8-5s8 2 8 5v2h-4V9H8v2H4zM6 13h12l2 7H4z"/></svg>+1.555.210.0400 x123</li>
        <li><svg viewBox="0 0 24 24" aria-hidden="true"><path d="M7 2h10a1 1 0 0 1 1 1v18a1 1 0 0 1-1 1H7a1 1 0 0 1-1-1V3a1 1 0 0 1 1-1zm1 3v12h8V5zm4 14a1 1 0 1 0 0 .01z"/></svg>+1.555.123.4567</li>
        <li><svg viewBox="0 0 24 24" aria-hidden="true"><path d="M2 5h20v14H2zm2 2v.5l8 5 8-5V7z"/></svg>info@veldmarksupplies.com</li>
        <li><svg viewBox="0 0 24 24" aria-hidden="true"><path d="M12 2a10 10 0 1 0 0 20 10 10 0 0 0 0-20zm-1 17.9A8 8 0 0 1 4.1 11H8c.2 3.3 1.2 6.5 3 8.9zM8 9H4.1A8 8 0 0 1 11 4.1C9.2 6.5 8.2 9.7 8 9zm2 0c.2-2.6 1-5 2-6.6 1 1.6 1.8 4 2 6.6zm0 2h4c-.2 2.6-1 5-2 6.6-1-1.6-1.8-4-2-6.6zm3 8.9c1.8-2.4 2.8-5.6 3-8.9h3.9a8 8 0 0 1-6.9 8.9zM16 9c-.2-.7-1.2-2.5-3-4.9A8 8 0 0 1 19.9 9z"/></svg>www.veldmarksupplies.com</li>
      </ul>
    </div>
    <p class="address">240 Ridgeline Court Halden, TX 79701 USA</p>
  </section>
</body>
</html>
```